Business card for law firm

Need business card for new law firm. Think confident, authoritative, conservative, but not stuffy or old-fashioned.

Contact Information for Business Card

Content for card - logo (uploaded), plus the following:

Paul Whitcombe (larger font)
Managing Partner (larger font, but not as large as name)
Level 9, 7 Ferris Lane
Sydney NSW 2000
Main Tel 02 9364 2710
Direct Tel 02 8472 3159
Email paul@qvlegal.com.au
www.qvlegal.com.au

Letterhead design should include logo plus:
Level 9, 7 Ferris Lane
Sydney NSW 2000
Tel 02 8472 3159
www.qvlegal.com.au

```html
<!DOCTYPE html>
<html lang="en">
<head>
<meta charset="utf-8">
<title>Quayvale Legal – Business Card</title>
<link rel="stylesheet" href="https://fonts.googleapis.com/css2?family=Cinzel:wght@400;600&family=Open+Sans:wght@400&display=swap">
<style>
  :root {
    --navy: #0f1f5c;
    --ink: #141414;
    --paper: #ffffff;
    --stage: #1e1e20;
    --mist: #e3e6ee;
    --panel: #050505;
    --serif: "Cinzel", "Times New Roman", serif;
    --sans: "Open Sans", Arial, sans-serif;
  }
  * { box-sizing: border-box; margin: 0; padding: 0; }
  html, body { width: 1200px; height: 960px; overflow: hidden; }
  body {
    background: var(--stage);
    display: flex;
    flex-direction: column;
    align-items: center;
    justify-content: center;
    gap: 40px;
  }
  .card {
    position: relative;
    width: 760px;
    height: 420px;
    background: var(--paper);
    overflow: hidden;
  }

  /* Wordmark */
  .wordmark { display: flex; flex-direction: column; align-items: center; }
  .wordmark__square { width: 46px; height: 46px; background: var(--navy); margin-bottom: 14px; }
  .wordmark__name {
    font-family: var(--serif);
    font-weight: 600;
    color: var(--ink);
    font-size: 40px;
    letter-spacing: 2px;
    line-height: 1;
  }
  .wordmark__sub {
    font-family: var(--serif);
    font-weight: 600;
    color: var(--ink);
    font-size: 13px;
    letter-spacing: 12px;
    margin-top: 6px;
    padding-left: 12px;
  }

  /* Front */
  .card--front { display: flex; flex-direction: column; align-items: center; justify-content: center; }
  .card--front .website {
    font-family: var(--sans);
    font-size: 15px;
    letter-spacing: 3px;
    color: var(--ink);
    margin-top: 18px;
  }

  /* Back */
  .card--back .wordmark { position: absolute; left: 70px; top: 40px; }
  .card--back .wordmark__name { font-size: 34px; }
  .card--back .wordmark__square { width: 40px; height: 40px; margin-bottom: 12px; }
  .decor-square {
    position: absolute; left: 560px; top: 120px;
    width: 150px; height: 180px; background: var(--mist);
  }
  .person { position: absolute; right: 44px; top: 140px; text-align: right; }
  .person__name {
    font-family: var(--serif); font-weight: 600;
    color: var(--navy); font-size: 22px; letter-spacing: 1px;
  }
  .person__title {
    font-family: var(--serif); font-weight: 400;
    color: var(--ink); font-size: 18px; letter-spacing: 1px; margin-top: 2px;
  }
  .contact-band {
    position: absolute; left: 0; top: 230px;
    width: 505px; height: 190px;
    background: var(--navy);
    border-top-right-radius: 32px;
    padding: 26px 0 0 40px;
    color: var(--paper);
    font-family: var(--sans); font-size: 15px;
    display: flex; flex-direction: column; gap: 10px;
  }
  .contact-row { display: flex; align-items: center; gap: 8px; }
  .contact-row .gap { width: 10px; }
  .icon { width: 14px; height: 14px; fill: none; stroke: var(--paper); stroke-width: 1.6; }
  .dark-panel {
    position: absolute; left: 528px; top: 268px;
    width: 232px; height: 152px;
    background: var(--panel);
    border-top-left-radius: 28px;
  }
</style>
</head>
<body>

  <section class="card card--front" aria-label="Business card front">
    <div class="wordmark">
      <div class="wordmark__square"></div>
      <div class="wordmark__name">QUAYVALE</div>
      <div class="wordmark__sub">LEGAL</div>
    </div>
    <p class="website">www.qvlegal.com.au</p>
  </section>

  <section class="card card--back" aria-label="Business card back">
    <div class="decor-square"></div>
    <div class="wordmark">
      <div class="wordmark__square"></div>
      <div class="wordmark__name">QUAYVALE</div>
      <div class="wordmark__sub">LEGAL</div>
    </div>

    <div class="person">
      <p class="person__name">Paul Whitcombe</p>
      <p class="person__title">Managing Partner</p>
    </div>

    <div class="contact-band">
      <p class="contact-row">
        <svg class="icon" viewBox="0 0 16 16"><circle cx="8" cy="8" r="7"/><path d="M5 4.5c0 4 2.5 6.5 6.5 6.5l.5-1.5-2-1-1 1c-1.5-.7-2.3-1.5-3-3l1-1-1-2z"/></svg>
        <span>02 9364 2710</span><span class="gap"></span>
        <svg class="icon" viewBox="0 0 16 16"><circle cx="8" cy="8" r="7"/><path d="M5 4.5c0 4 2.5 6.5 6.5 6.5l.5-1.5-2-1-1 1c-1.5-.7-2.3-1.5-3-3l1-1-1-2z"/></svg>
        <span>02 8472 3159</span>
      </p>
      <p class="contact-row">
        <svg class="icon" viewBox="0 0 16 16"><rect x="1.5" y="3.5" width="13" height="9"/><path d="M1.5 3.5 8 9l6.5-5.5"/></svg>
        <span>paul@qvlegal.com.au</span><span class="gap"></span>
        <svg class="icon" viewBox="0 0 16 16"><circle cx="8" cy="8" r="6.5"/><ellipse cx="8" cy="8" rx="3" ry="6.5"/><path d="M1.5 8h13"/></svg>
        <span>www.qvlegal.com.au</span>
      </p>
      <p class="contact-row">Level 9, 7 Ferris Lane, Sydney NSW 2000</p>
    </div>

    <div class="dark-panel"></div>
  </section>

</body>
</html>
```